Email Marketing Campaign Brief

We want to do an email marketing campaign around our consulting services. The attached documents provide back ground on our work but additional copy can be found below:

KV7lr is committed to helping you, the educator, make informed buying decisions based on local control and independent reviews through a simple, impartial and an effective approach.
In education, there exists a vast array of educational solutions – such as reading, science, language arts, and math curricula; school-wide reform programs; interventions; after-school programs; and new educational technologies. In the marketplace, providers could, and most do, claim to be able to improve educational outcomes and, in many cases, they all pretend to be supported by evidence. But a cursory review reveals that most evidence consists of poorly designed or advocacy-driven studies with some providers having such inadequate research as could only be described as case studies.

So the problem for State and local education officials is that they must sort through a myriad of such claims to decide which solutions merit consideration for their schools and classrooms. One US official stated the problem saying “many of these practitioners have seen interventions (solutions), introduced with great fanfare as being able to produce dramatic gains, come and go over the years, yielding little in the way of positive and lasting change – a perception confirmed by the flat achievement results over the past 30 years in the Federal Survey of Scholastic Attainment long-term trend”

KV7lr is a process by which we make you, the educator, the locus of control

OUR Approach:
With four simple, yet highly effective steps, KV7lr guides educators through an informed buying process that’s based on local control and review.

Step 1 — Research, Review, and Evaluation Criteria

Step 2 — Cost / Benefit Analysis

Step 3 — Education Survey & Culture Scan

Step 4 — Negotiation & Representation

Target Market(s)

Education

Industry/Entity Type

Marketing

Font styles to use
Sans Serif

Colors
f9b46a
f37122

Requirements
Must have
• HTML format that can be used in an Email Campaign
Nice to have
• Additional Copy in Word

```html
<!DOCTYPE html>
<html lang="en">
<head>
<meta charset="utf-8">
<title>KV7lr – Informed Buying for Educators</title>
<link href="https://fonts.googleapis.com/css2?family=Baloo+2:wght@700;800&family=Quicksand:wght@300;400;500&family=Open+Sans:wght@400;600;700&display=swap" rel="stylesheet">
<style>
:root{
  --orange:#f15a22;
  --orange-deep:#e8501c;
  --amber:#f7a21b;
  --peach:#f9b46a;
  --red:#d8333f;
  --cyan:#1fb5e0;
  --green:#1f7f5c;
  --blue:#1a9ed8;
  --ink:#2b2b2b;
  --grey:#555;
  --white:#fff;
}
*{box-sizing:border-box;margin:0;padding:0}
html,body{width:702px;height:1200px;overflow:hidden;background:var(--white)}
body{font-family:"Open Sans",sans-serif;color:var(--ink)}
.canvas{position:relative;width:702px;height:1200px;overflow:hidden}
.shapes{position:absolute;left:0;top:0}
.abs{position:absolute}

.nav-label{font-family:"Baloo 2",sans-serif;font-weight:700;font-size:19px;color:var(--white);top:8px;letter-spacing:.2px}
.brand{left:42px;top:40px;font-family:"Quicksand",sans-serif;font-weight:500;font-size:30px;color:var(--white);display:flex;align-items:center;gap:8px}
.brand-dot{width:18px;height:18px;border-radius:50%;background:var(--white)}

.hero-title{left:0;width:702px;top:308px;text-align:center;font-family:"Baloo 2",sans-serif;font-weight:800;font-size:26px;color:var(--white);text-shadow:0 2px 3px rgba(0,0,0,.55)}
.hero-sub{left:0;width:702px;top:344px;text-align:center;font-family:"Baloo 2",sans-serif;font-weight:700;font-size:16px;color:var(--white);text-shadow:0 1px 3px rgba(0,0,0,.55)}

.intro{top:399px;width:286px;font-size:6.6px;line-height:8.3px;text-align:justify;color:#222}
.intro p{margin-bottom:0}
.intro .gap{margin-top:8px}
.intro b{color:var(--orange);font-weight:700}

.approach-title{left:0;width:702px;top:505px;text-align:center;font-family:"Baloo 2",sans-serif;font-weight:800;font-size:16px;color:#333}
.approach-sub{left:0;width:702px;top:524px;text-align:center;font-family:"Quicksand",sans-serif;font-weight:500;font-size:10px;line-height:12.5px;color:#333}

.step-num{font-family:"Baloo 2",sans-serif;font-weight:800;color:var(--red);text-align:center}
.step-title{font-family:"Quicksand",sans-serif;font-weight:400;color:var(--white);text-transform:uppercase;font-size:16.5px;line-height:21px}
.step-list{list-style:none;font-family:"Quicksand",sans-serif;font-weight:400;font-size:8.6px;line-height:11px;color:var(--white)}
.step-list li{position:relative;padding-left:11px}
.step-list li::before{content:"";position:absolute;left:1px;top:2.5px;width:6px;height:6px;border-radius:50%;background:rgba(255,255,255,.85)}
.read-more{background:var(--white);color:var(--orange);font-family:"Quicksand",sans-serif;font-weight:500;font-size:10px;width:66px;height:20px;line-height:20px;text-align:center}

.impl-title{left:0;width:702px;top:1010px;text-align:center;font-family:"Baloo 2",sans-serif;font-weight:800;font-size:22px;color:var(--orange)}
.impl-sub{left:0;width:702px;top:1035px;text-align:center;font-family:"Quicksand",sans-serif;font-weight:500;font-size:13px;color:#333}
.cta{left:0;width:702px;top:1070px;text-align:center;font-size:11.5px;line-height:15px;color:#222}
.cta b{color:var(--orange)}
.cta strong{font-weight:700}

.footer-text{left:62px;top:1128px;font-family:"Quicksand",sans-serif;font-size:10px;color:var(--white);display:flex;align-items:baseline;gap:8px}
.footer-text .phone{font-family:"Baloo 2",sans-serif;font-weight:700;font-size:15px}
.site{left:516px;top:1165px;font-size:10px;font-weight:600;color:#444}
</style>
</head>
<body>
<div class="canvas">

<svg class="shapes" width="702" height="1200" viewBox="0 0 702 1200" xmlns="http://www.w3.org/2000/svg">
  <!-- top navigation tabs -->
  <polygon points="214,0 402,0 380,52 214,52" fill="#f7a21b"/>
  <polygon points="402,0 564,0 542,52 380,52" fill="#d8333f"/>
  <polygon points="564,0 702,0 702,52 542,52" fill="#1fb5e0"/>
  <!-- brand banner -->
  <polygon points="0,26 222,26 240,65 222,104 0,104" fill="#e8501c"/>

  <!-- hero image area -->
  <defs>
    <linearGradient id="heroFill" x1="0" y1="0" x2="1" y2="1">
      <stop offset="0" stop-color="#f2e6c9"/>
      <stop offset=".45" stop-color="#d9a873"/>
      <stop offset=".7" stop-color="#7a6fb8"/>
      <stop offset="1" stop-color="#c9413a"/>
    </linearGradient>
  </defs>
  <path role="img" aria-label="Photo of five young children leaning in together over a book in a bright classroom" d="M24,76 L678,76 L678,360 Q351,410 24,360 Z" fill="url(#heroFill)"/>

  <!-- step 1 panel -->
  <path d="M18,590 Q40,560 78,560 Q110,548 150,556 Q180,564 200,576 Q214,584 224,572 Q232,566 234,578 L234,842 Q126,854 26,852 Z" fill="#1f7f5c"/>
  <!-- step 3 panel -->
  <path d="M470,578 Q500,568 540,574 Q580,580 600,566 Q640,546 672,556 Q686,566 686,600 L676,852 Q576,850 472,842 Z" fill="#1a9ed8"/>
  <!-- step 2 panel -->
  <path d="M243,600 L252,596 L262,599 L274,595 L288,598 L300,594 L316,598 L330,595 L346,599 L372,594 L392,598 L410,595 L428,599 L444,594 L458,597 L458,824 L243,824 Z" fill="#e8501c"/>
  <!-- step 4 panel -->
  <path d="M192,822 L508,822 Q514,824 514,832 L508,954 Q506,964 496,964 L200,964 Q190,964 190,954 L186,832 Q186,822 192,822 Z" fill="#f7a21b"/>

  <!-- number circles -->
  <circle cx="52" cy="572" r="25" fill="#fff" stroke="#f15a22" stroke-width="3"/>
  <circle cx="350" cy="600" r="21" fill="#fff" stroke="#f15a22" stroke-width="3"/>
  <circle cx="640" cy="572" r="25" fill="#fff" stroke="#f15a22" stroke-width="3"/>
  <circle cx="349" cy="822" r="21" fill="#fff" stroke="#f15a22" stroke-width="3"/>

  <!-- icons -->
  <g stroke="#fff" stroke-width="2" fill="none">
    <circle cx="46" cy="804" r="8"/>
    <line x1="52" y1="810" x2="60" y2="818" stroke-width="3"/>
    <path d="M296,770 a7,7 0 1 1 8,0 v4 h-8 z"/>
    <line x1="297" y1="778" x2="303" y2="778"/>
    <line x1="300" y1="755" x2="300" y2="752"/>
    <line x1="288" y1="762" x2="285" y2="760"/>
    <line x1="312" y1="762" x2="315" y2="760"/>
    <line x1="286" y1="768" x2="282" y2="768"/>
    <line x1="314" y1="768" x2="318" y2="768"/>
    <circle cx="552" cy="810" r="7.5" stroke-width="3.5" stroke-dasharray="3 2"/>
    <circle cx="552" cy="810" r="5"/>
    <rect x="279" y="934" width="24" height="15" rx="1"/>
    <line x1="273" y1="952" x2="309" y2="952"/>
  </g>

  <!-- implementation divider and arrow -->
  <line x1="162" y1="974" x2="528" y2="974" stroke="#444" stroke-width="1"/>
  <polygon points="272,975 424,975 348,1006" fill="#f9b46a"/>
  <line x1="162" y1="1060" x2="528" y2="1060" stroke="#444" stroke-width="1"/>

  <!-- footer bar -->
  <rect x="50" y="1112" width="606" height="48" fill="#f37122"/>
  <rect x="50" y="1112" width="606" height="3" fill="#f9b46a"/>
  <g fill="#fff">
    <rect x="500" y="1122" width="26" height="26" rx="4"/>
    <rect x="532" y="1122" width="26" height="26" rx="4"/>
    <rect x="564" y="1122" width="26" height="26" rx="4"/>
    <rect x="596" y="1122" width="26" height="26" rx="4"/>
  </g>
</svg>

<div class="abs nav-label" style="left:260px">Research</div>
<div class="abs nav-label" style="left:444px">Policy</div>
<div class="abs nav-label" style="left:592px">Practice</div>

<div class="abs brand"><span class="brand-dot"></span>KV7lr</div>

<div class="abs hero-title">We help you to build geniuses</div>
<div class="abs hero-sub">Research, Teaching, Learning</div>

<div class="abs intro" style="left:56px">
  <p><b>KV7lr</b> is committed to helping you, the educator; make informed buying decisions based on local control and independent reviews through a simple, impartial and an effective approach.</p>
  <p>In education, there exists a vast array of educational solutions – such as reading, science, language arts, and math curricula; school-wide reform programs; interventions; after-school programs; and new educational technologies. In the marketplace, providers could, and most do, claim to be able to improve educational outcomes and, in many cases, they all pretend to be supported by evidence. But a cursory review reveals that most evidence consists of poorly designed or advocacy-driven studies with some providers having such inadequate research as could only be described as case studies.</p>
</div>
<div class="abs intro" style="left:360px">
  <p>So the problem for State and local education officials is that they must sort through a myriad of such claims to decide which solutions merit consideration for their schools and classrooms.</p>
  <p>One US official stated the problem saying “many of these practitioners have seen interventions (solutions), introduced with great fanfare as being able to produce dramatic gains, come and go over the years, yielding little in the way of positive and lasting change – a perception confirmed by the flat achievement results over the past 30 years in the Federal Survey of Scholastic Attainment long-term trend”.</p>
  <p class="gap"><b>KV7lr</b> is a process by which we make you, the educator, the focus of control.</p>
</div>

<div class="abs approach-title">OUR Approach:</div>
<div class="abs approach-sub">With four simple, yet highly effective steps, KV7lr guides educators through<br>an informed buying process that’s based on local control and review.</div>

<div class="abs step-num" style="left:27px;top:550px;width:50px;font-size:34px;line-height:44px">1</div>
<div class="abs step-num" style="left:329px;top:583px;width:42px;font-size:28px;line-height:36px">2</div>
<div class="abs step-num" style="left:615px;top:550px;width:50px;font-size:34px;line-height:44px">3</div>
<div class="abs step-num" style="left:328px;top:805px;width:42px;font-size:28px;line-height:36px">4</div>

<div class="abs step-title" style="left:26px;top:612px;width:210px">Research, Review, and<br>Evaluation Criteria</div>
<ul class="abs step-list" style="left:32px;top:661px;width:196px">
  <li>District needs analysis</li>
  <li style="margin-top:12px">Program reviews and alignment to need</li>
  <li style="margin-top:12px">Independent evaluation / data informed decisions</li>
</ul>
<div class="abs read-more" style="left:68px;top:800px">READ MORE</div>

<div class="abs step-title" style="left:243px;top:632px;width:215px;text-align:center">Cost / Benefit Analysis</div>
<ul class="abs step-list" style="left:259px;top:661px;width:190px">
  <li>Cost alignment based on research, review and evaluation of programs</li>
  <li style="margin-top:9px">Program cost by product offering and alignment to identified needs</li>
  <li style="margin-top:9px">Summary of cost, data and return on investment</li>
</ul>
<div class="abs read-more" style="left:318px;top:766px">READ MORE</div>

<div class="abs step-title" style="left:470px;top:612px;width:216px;text-align:center">Education Survey<br>and Culture Scan</div>
<ul class="abs step-list" style="left:484px;top:661px;width:202px">
  <li>District observation and perception survey</li>
  <li style="margin-top:11px">Culture scan to identify education best practices</li>
  <li style="margin-top:11px">Match to strategic plan goals and objectives</li>
</ul>
<div class="abs read-more" style="left:574px;top:800px">READ MORE</div>

<div class="abs step-title" style="left:186px;top:845px;width:326px;text-align:center">Negotiation<br>and Representation</div>
<ul class="abs step-list" style="left:186px;top:894px;width:326px;text-align:center;line-height:11px">
  <li style="display:inline-block">Conduct Provider review and presentation</li><br>
  <li style="display:inline-block">Representation for content and program negotiations</li><br>
  <li style="display:inline-block">Support district in independent decision-making process</li>
</ul>
<div class="abs read-more" style="left:316px;top:934px">READ MORE</div>

<div class="abs impl-title">PROGRAM IMPLEMENTATION</div>
<div class="abs impl-sub">Independent Review Connected to School District Need and Stakeholder</div>

<div class="abs cta">Let <b>KV7lr</b> help you make informed buying decisions.<br><strong>Contact us today for a no-cost consultation</strong></div>

<div class="abs footer-text"><span>Have a question? It is great to hear from you:</span><span class="phone">555.010.0147</span></div>
<div class="abs site">www.KV7lr.com</div>

</div>
</body>
</html>
```